Professional Package for CPA Firm

We would like a stationery design for our new CPA Firm based in Atlanta, GA called 'Vale 8'. We work with investors to help grow investments, tax free. We would like the design to have a professional/minimal look with a 'wow' factor. We need 9.5″ x 4.125″, 9x12, and 10x13 mailing envelopes, business cards, and a letterhead. We have a logo that is already complete. For the letterhead, we would like to have space to put credentials at the bottom of the page

Industry/Entity Type

CPA, Accounting

```html
<!DOCTYPE html>
<html lang="en">
<head>
<meta charset="utf-8">
<title>Vale 8 — Business Cards</title>
<link rel="stylesheet" href="https://fonts.googleapis.com/css2?family=Open+Sans:wght@400;600;700&display=swap">
<style>
  :root {
    --navy: #0f3350;
    --teal: #27b3b8;
    --sky: #22b3d4;
    --coral: #f1565c;
    --paper: #ffffff;
    --ink: #5c6470;
    --backdrop: #e9ebee;
  }
  * { box-sizing: border-box; margin: 0; padding: 0; }
  html, body {
    width: 1200px; height: 874px; overflow: hidden;
    background: var(--backdrop);
    font-family: "Open Sans", sans-serif;
  }
  .canvas { position: relative; width: 1200px; height: 874px; }

  .card {
    position: absolute;
    width: 620px; height: 354px;
    border-radius: 18px;
    overflow: hidden;
    box-shadow: 0 10px 26px rgba(15, 51, 80, 0.18);
  }

  /* Front */
  .card-front {
    left: 380px; top: 48px;
    background: var(--navy);
    display: flex; align-items: center; justify-content: center;
  }
  .brand { display: flex; flex-direction: column; align-items: center; }
  .brand-row { display: flex; align-items: center; gap: 14px; }
  .brand-dot {
    width: 22px; height: 22px; border-radius: 50%;
    background: var(--coral);
  }
  .brand-name {
    font-weight: 700; font-size: 64px; letter-spacing: 3px; line-height: 1;
    color: var(--sky);
  }
  .brand-tagline {
    margin-top: 10px;
    font-size: 16px; letter-spacing: 3px;
    color: var(--sky);
  }

  /* Back */
  .card-back { left: 200px; top: 470px; background: var(--paper); }
  .wave { position: absolute; inset: 0; width: 620px; height: 354px; }
  .card-back .brand {
    position: absolute; left: 40px; top: 30px; align-items: flex-start;
  }
  .card-back .brand-name { color: var(--paper); font-size: 50px; }
  .card-back .brand-tagline { color: var(--paper); font-size: 13px; letter-spacing: 2px; margin-top: 8px; }
  .card-back .brand-dot { width: 18px; height: 18px; }

  .contact {
    position: absolute; right: 34px; bottom: 18px;
    text-align: right;
  }
  .person-name {
    font-size: 19px; line-height: 1.35; letter-spacing: 1px; color: var(--teal); font-weight: 400;
  }
  .person-role { font-size: 13px; line-height: 1.4; color: var(--coral); margin-bottom: 6px; }
  .address { font-size: 13px; color: var(--ink); line-height: 1.3; margin-bottom: 8px; }
  .contact-list { list-style: none; }
  .contact-list li {
    display: flex; justify-content: flex-end; align-items: center; gap: 8px;
    font-size: 13px; color: var(--ink); line-height: 1.4;
  }
  .icon { width: 12px; height: 12px; fill: var(--coral); flex: none; }
</style>
</head>
<body>
<main class="canvas">

  <section class="card card-front" aria-label="Business card front">
    <div class="brand">
      <div class="brand-row">
        <span class="brand-dot"></span>
        <span class="brand-name">Vale 8</span>
      </div>
      <p class="brand-tagline">CPAs and Tax Advisors</p>
    </div>
  </section>

  <section class="card card-back" aria-label="Business card back">
    <svg class="wave" viewBox="0 0 620 354" preserveAspectRatio="none" aria-hidden="true">
      <path fill="var(--teal)" transform="translate(0,14)" d="M0 0 H620 V100 C520 82 430 122 330 184 C250 234 170 258 90 232 C50 218 20 200 0 186 Z"/>
      <path fill="var(--coral)" transform="translate(0,7)" d="M0 0 H620 V100 C520 82 430 122 330 184 C250 234 170 258 90 232 C50 218 20 200 0 186 Z"/>
      <path fill="var(--navy)" d="M0 0 H620 V100 C520 82 430 122 330 184 C250 234 170 258 90 232 C50 218 20 200 0 186 Z"/>
    </svg>

    <div class="brand">
      <div class="brand-row">
        <span class="brand-dot"></span>
        <span class="brand-name">Vale 8</span>
      </div>
      <p class="brand-tagline">CPAs and Tax Advisors</p>
    </div>

    <div class="contact">
      <h2 class="person-name">DANIEL BROOKS</h2>
      <p class="person-role">President</p>
      <p class="address">4120 Birchwood Avenue<br>Atlanta, Georgia 30318</p>
      <ul class="contact-list">
        <li>404-555-0182
          <svg class="icon" viewBox="0 0 12 12" aria-hidden="true"><path d="M2.5 1 L4.5 1 L5.2 3.6 L4 4.6 C4.6 6 6 7.4 7.4 8 L8.4 6.8 L11 7.5 L11 9.5 C11 10.3 10.3 11 9.5 11 C5 11 1 7 1 2.5 C1 1.7 1.7 1 2.5 1 Z"/></svg>
        </li>
        <li>404-555-0137
          <svg class="icon" viewBox="0 0 12 12" aria-hidden="true"><path d="M3.5 0.5 H8.5 A1 1 0 0 1 9.5 1.5 V10.5 A1 1 0 0 1 8.5 11.5 H3.5 A1 1 0 0 1 2.5 10.5 V1.5 A1 1 0 0 1 3.5 0.5 Z M3.8 1.8 V9 H8.2 V1.8 Z M6 9.6 A0.6 0.6 0 1 0 6 10.8 A0.6 0.6 0 1 0 6 9.6 Z"/></svg>
        </li>
        <li>info@vale8.com
          <svg class="icon" viewBox="0 0 12 12" aria-hidden="true"><path d="M1 2.5 H11 V9.5 H1 Z M1.8 3.2 L6 6.4 L10.2 3.2 Z"/></svg>
        </li>
        <li>www.vale8.com
          <svg class="icon" viewBox="0 0 12 12" aria-hidden="true"><circle cx="6" cy="6" r="5"/><path d="M1 6 H11 M6 1 C3.8 3.5 3.8 8.5 6 11 M6 1 C8.2 3.5 8.2 8.5 6 11" stroke="#fff" stroke-width="0.8" fill="none"/></svg>
        </li>
      </ul>
    </div>
  </section>

</main>
</body>
</html>
```